Business cards for 3 Realtors at one brokerage

We will need a business card template that can be projected on 3 business cards. Harborline Realty & Investment Corp. has 3 realtors on staff Dane, Owen, and Miles. We all want a business card that shows our new logo and information. I will attach many versions of our Logo as well as head shots for each realtor (Owen- Long hair, youngest. Miles- Suit jacket, parted hair cut. Dane- Angled Pose, Shirt and Tie.) I have attached our information below.

Dane Foskett
801-555-0147
dane@harborlinehomesite.com
Principal Broker

Miles Tandrow
801-555-0162
miles@harborlinehomesite.com
Real Estate Agent

Owen Tandrow
801-555-0138
owen@harborlinehomesite.com
Real Estate Agent

Harborline Realty & Investment Corp.
HarborlineHomesite.com
5286 N 7200 Suite 208-617, South Jordan, UT 84009

Please feel free to reach out with any questions, comments, or concerns.

```html
<!DOCTYPE html>
<html lang="en">
<head>
<meta charset="utf-8">
<title>Harborline Realty – Business Card</title>
<link rel="stylesheet" href="https://fonts.googleapis.com/css2?family=Montserrat:wght@500;600;700&family=Arimo:wght@400&display=swap">
<style>
  :root {
    --canvas: #a4a4a4;
    --card-white: #ffffff;
    --brand-blue: #38aaf6;
    --brand-grey: #6a6a6a;
    --photo-grey: #717171;
    --text-white: #ffffff;
    --rule: rgba(255,255,255,0.55);
  }
  html, body {
    margin: 0; padding: 0;
    width: 1200px; height: 1200px;
    overflow: hidden;
    background: var(--canvas);
  }
  .stage { position: relative; width: 1200px; height: 1200px; }
  .card {
    position: absolute;
    top: 303px;
    height: 594px;
    box-shadow: 3px 4px 8px rgba(0,0,0,0.35);
    overflow: hidden;
  }
  /* Front: brand side */
  .card--front { left: 200px; width: 369px; background: var(--card-white); }
  .brand-mark {
    position: absolute; left: 125px; top: 204px;
    width: 118px; height: 118px;
  }
  .brand-name {
    position: absolute; left: 0; right: 0;
    text-align: center;
    font-family: "Montserrat", sans-serif;
    font-weight: 500;
    color: var(--brand-grey);
    margin: 0;
    white-space: nowrap;
  }
  .brand-name__main { top: 336px; font-size: 29px; letter-spacing: 0.6px; line-height: 34px; }
  .brand-name__sub { top: 375px; font-size: 13px; letter-spacing: 4.3px; line-height: 16px; }
  .front-web {
    position: absolute; left: 0; right: 0; top: 531px;
    text-align: center;
    font-family: "Arimo", sans-serif;
    font-size: 16px;
    color: var(--brand-grey);
  }
  .front-web__domain { color: var(--brand-blue); }

  /* Back: agent side */
  .card--agent { left: 599px; width: 364px; background: var(--brand-blue); }
  .agent-photo {
    position: absolute; left: 0; top: 0;
    width: 364px; height: 319px;
    background: radial-gradient(ellipse at 50% 55%, #8a7d74 0%, #787370 38%, var(--photo-grey) 70%);
  }
  .agent-name {
    position: absolute; left: 0; right: 0; top: 347px;
    margin: 0;
    font-family: "Montserrat", sans-serif;
    font-weight: 700; font-size: 22px; line-height: 24px;
    color: var(--text-white);
    text-align: center;
  }
  .agent-title {
    position: absolute; left: 0; right: 0; top: 369px;
    font-family: "Arimo", sans-serif; font-size: 16px; line-height: 20px;
    color: var(--text-white); text-align: center;
  }
  .icon-row { position: absolute; left: 0; top: 404px; width: 364px; height: 30px; }
  .contact-lines, .address-lines {
    position: absolute; left: 0; right: 0;
    font-family: "Arimo", sans-serif;
    font-size: 16px; line-height: 21.7px;
    color: var(--text-white); text-align: center;
  }
  .contact-lines { top: 438px; }
  .address-lines { top: 525px; }
  .divider {
    position: absolute; left: 88px; width: 189px; top: 515px;
    height: 1px; background: var(--rule);
  }
</style>
</head>
<body>
<div class="stage">

  <section class="card card--front">
    <svg class="brand-mark" viewBox="0 0 118 118" aria-hidden="true">
      <circle cx="59" cy="59" r="56" fill="none" stroke="var(--brand-blue)" stroke-width="4"/>
    </svg>
    <p class="brand-name brand-name__main">HARBORLINE REALTY</p>
    <p class="brand-name brand-name__sub">&amp; INVESTMENT CORP.</p>
    <div class="front-web">www.<span class="front-web__domain">HarborlineHomesite</span>.com</div>
  </section>

  <section class="card card--agent">
    <div class="agent-photo" role="img" aria-label="Headshot of Owen Tandrow, smiling, long hair, white open-collar shirt, on a grey backdrop"></div>

    <h1 class="agent-name">OWEN TANDROW</h1>
    <div class="agent-title">Real Estate Agent</div>

    <svg class="icon-row" viewBox="0 0 364 30" aria-hidden="true">
      <line x1="87" y1="15" x2="139" y2="15" stroke="var(--rule)" stroke-width="1"/>
      <line x1="231" y1="15" x2="277" y2="15" stroke="var(--rule)" stroke-width="1"/>
      <rect x="142" y="2" width="25" height="25" rx="3" fill="#fff"/>
      <path d="M148 12c0-3 4-4 6.5-4s6.5 1 6.5 4l-2.5 1-1-2h-6l-1 2z" fill="var(--brand-blue)"/>
      <rect x="149" y="14" width="11" height="8" rx="1" fill="var(--brand-blue)"/>
      <rect x="171" y="2" width="25" height="25" rx="3" fill="#fff"/>
      <rect x="176" y="9" width="15" height="11" fill="none" stroke="var(--brand-blue)" stroke-width="1.6"/>
      <path d="M176 9l7.5 6 7.5-6" fill="none" stroke="var(--brand-blue)" stroke-width="1.6"/>
      <rect x="200" y="2" width="25" height="25" rx="3" fill="#fff"/>
      <circle cx="212.5" cy="14.5" r="7.5" fill="var(--brand-blue)"/>
      <path d="M208 11c2 0 3 1 3 3s-2 2-2 4M215 9c-1 2 1 3 2 4" fill="none" stroke="#fff" stroke-width="1.3"/>
    </svg>

    <div class="contact-lines">
      801-555-0138<br>
      owen@harborlinehomesite.com<br>
      www.HarborlineHomesite.com
    </div>
    <div class="divider"></div>
    <div class="address-lines">
      5286 N 7200 Suite 208-617<br>
      Cedar Hollow, UT 84190
    </div>
  </section>

</div>
</body>
</html>
```